Business card for Eyelash extension salon in Beverly Hills,California USA

We need new business card for our salon in Beverly Hills. The salon name is 'Lashvera' . We would like to have...Business name: Lashvera Name of person: will provide later Address 4720 N.Alder Crest Ave Beverly Hills , CA 90210 Phone: will provide later (Text only) Web: www.lashverastudio.example Snapgrid icon, Circlebook icon follow us for seasonal campaign and news @lashverastudiolounge Design should look elegant, high-end, clean, simple, cohesive with my brand. Please refer my brand board. Business name color will be metallic bronzy color. Im thinking grey background or white background. Thanks

Target Market(s)

25-35. Gender neutral. People who are in Entertainment business industry.
This is High-end Eyelash extension salon in Beverly Hills

Industry/Entity Type

Beauty Salon

Contact Information for Business Card

Business name: Lashvera
Name of person: will provide later
Address 4720 N.Alder Crest Ave Beverly Hills , CA 90210
Phone: will provide later (Text only)
Web: www.lashverastudio.example
Snapgrid icon, Circlebook icon
follow us for seasonal campaign and news @lashverastudiolounge

Requirements
Must have
• Beautiful, elegant, clean and simple look but very attractive and modern
Should not have
• We don't like too clutter, too busy designs.

```html
<!DOCTYPE html>
<html lang="en">
<head>
<meta charset="utf-8">
<title>Lashvera Business Card</title>
<link rel="stylesheet" href="https://fonts.googleapis.com/css2?family=Josefin+Sans:wght@300&family=Libre+Baskerville:wght@400;700&display=swap">
<style>
  :root {
    --canvas: #e4e4e4;
    --card-white: #ffffff;
    --card-grey: #aaaaaa;
    --bronze: #8a6a55;
    --muted: #a8a8a8;
    --ink: #555555;
    --white: #ffffff;
  }
  * { margin: 0; padding: 0; box-sizing: border-box; }
  html, body { width: 1200px; height: 960px; overflow: hidden; }
  body { background: var(--canvas); position: relative; }

  .card { position: absolute; width: 600px; height: 343px; overflow: hidden; }
  .card-front { left: 302px; top: 122px; background: var(--card-white); }
  .card-back { left: 299px; top: 495px; background: var(--card-grey); }

  .portrait-area {
    position: absolute; right: 0; top: 0; width: 190px; height: 100%;
    background: linear-gradient(90deg, #ffffff 0%, #f3f3f3 30%, #ececec 100%);
  }

  .wordmark {
    position: absolute; left: 40px; top: 42px; width: 160px; text-align: center;
    font-family: "Josefin Sans", sans-serif; font-weight: 300; color: var(--bronze);
  }
  .wordmark-name { font-size: 40px; line-height: 1; }
  .wordmark-place { font-size: 7px; letter-spacing: 2px; margin-top: 8px; padding-left: 60px; }

  .holder { position: absolute; left: 40px; top: 154px; font-family: "Libre Baskerville", serif; }
  .holder-name { font-size: 22px; font-weight: 700; color: var(--bronze); letter-spacing: 1px; line-height: 1; }
  .holder-role { font-size: 14px; color: var(--muted); letter-spacing: 1px; margin-top: 2px; }

  .contact {
    position: absolute; left: 42px; top: 216px; list-style: none;
    font-family: "Josefin Sans", sans-serif; font-weight: 300; font-size: 14px; color: var(--ink);
    line-height: 18.5px;
  }
  .contact .gap { margin-top: 2px; }

  .back-wordmark {
    position: absolute; left: 0; top: 72px; width: 100%; text-align: center;
    font-family: "Josefin Sans", sans-serif; font-weight: 300; color: var(--white);
  }
  .back-wordmark-name { font-size: 96px; line-height: 1; letter-spacing: 1px; }
  .back-wordmark-place { font-size: 11px; letter-spacing: 3px; margin-top: 18px; padding-left: 80px; }

  .follow {
    position: absolute; left: 0; top: 294px; width: 100%;
    display: flex; justify-content: center; align-items: center; gap: 6px;
    font-family: "Libre Baskerville", serif; font-size: 13px; color: var(--white);
  }
  .social-dots { display: flex; gap: 3px; }
  .social-dot { width: 15px; height: 15px; border-radius: 50%; background: var(--white); }
</style>
</head>
<body>
  <section class="card card-front">
    <div class="portrait-area" role="img" aria-label="Soft black and white close-up of a model with closed eyes and long lashes"></div>
    <div class="wordmark">
      <div class="wordmark-name">Lashvera</div>
      <div class="wordmark-place">BEVERLY HILLS</div>
    </div>
    <div class="holder">
      <div class="holder-name">MIREI</div>
      <div class="holder-role">OWNER</div>
    </div>
    <ul class="contact">
      <li>4720 N.Alder Crest Ave</li>
      <li>Beverly Hills, CA 90210</li>
      <li class="gap">310.555.0142</li>
      <li>hello@lashverastudio.example</li>
      <li>www.lashverastudio.example</li>
    </ul>
  </section>

  <section class="card card-back">
    <div class="back-wordmark">
      <div class="back-wordmark-name">Lashvera</div>
      <div class="back-wordmark-place">BEVERLY HILLS</div>
    </div>
    <div class="follow">
      <span class="social-dots" aria-label="Circlebook, Snapgrid and Reviewly">
        <span class="social-dot"></span><span class="social-dot"></span><span class="social-dot"></span>
      </span>
      <span>follow us for seasonal campaign &amp; news @lashverastudiolounge</span>
    </div>
  </section>
</body>
</html>
```